Property Developer - Simple yet Sophisticated and Sharp Business Card

We are a medium sized property developer involved mainly in townhouse developments and land subdivisions.

The company is looking for a simple, sharp and sophisticated business card that will be given to contractors, land owners, financiers etc and thus will need to look professional.

Property development related graphics and art can be used, however the card is not to be too "busy" or crowded. Our company name is Kestrel Developments which could possibly be incorporated into the graphics or artwork.

Single sided and/or double sided designs will be acceptable.

A Simple, Sophisticated, Sharp design please!

Good Luck !

```html
<!DOCTYPE html>
<html lang="en">
<head>
<meta charset="utf-8">
<title>Kestrel Developments – Business Cards</title>
<link rel="stylesheet" href="https://fonts.googleapis.com/css2?family=Montserrat:wght@700&family=Open+Sans:wght@300;400;600&display=swap">
<style>
  :root {
    --page-bg: #e4e4e4;
    --brand-blue: #1a9ccd;
    --brand-blue-deep: #0f86b8;
    --brand-blue-light: #3cb0dc;
    --charcoal: #48484a;
    --text-grey: #4a4a4c;
    --white: #ffffff;
  }
  * { box-sizing: border-box; margin: 0; padding: 0; }
  html, body { width: 1200px; height: 697px; overflow: hidden; background: var(--page-bg); }
  .sheet { position: relative; width: 1200px; height: 697px; }

  .card { position: absolute; width: 584px; height: 331px; border-radius: 14px; overflow: hidden; }
  .card--front { left: 11px; background: linear-gradient(180deg, var(--brand-blue-light) 0%, var(--brand-blue) 50%, var(--brand-blue-deep) 100%); }
  .card--back { left: 605px; background: var(--white); }
  .row-1 { top: 11px; }
  .row-2 { top: 353px; }

  .brand { position: absolute; display: flex; align-items: center; font-family: "Montserrat", sans-serif; font-weight: 700; text-transform: uppercase; white-space: nowrap; }
  .brand__dot { border-radius: 50%; flex: none; }
  .card--front .brand { left: 47px; top: 131px; gap: 16px; color: var(--white); font-size: 31px; letter-spacing: 0.5px; }
  .card--front .brand__dot { width: 52px; height: 52px; background: var(--white); }
  .card--back .brand { left: 41px; top: 43px; gap: 12px; color: var(--text-grey); font-size: 22px; }
  .card--back .brand__dot { width: 40px; height: 40px; background: var(--brand-blue); }

  .person__name { position: absolute; left: 36px; top: 170px; font-family: "Open Sans", sans-serif; font-weight: 300; font-size: 28px; color: var(--brand-blue); text-transform: uppercase; letter-spacing: -0.5px; white-space: nowrap; }
  .person__rule { position: absolute; left: 0; top: 201px; }
  .person__title { position: absolute; left: 92px; top: 201px; width: 110px; height: 14px; line-height: 14px; text-align: center; font-family: "Open Sans", sans-serif; font-size: 9px; color: var(--white); text-transform: uppercase; }

  .divider { position: absolute; left: 245px; top: 177px; width: 1px; height: 70px; background: #c9c9c9; }

  .contact { position: absolute; left: 268px; top: 173px; list-style: none; font-family: "Open Sans", sans-serif; font-size: 12px; color: var(--text-grey); text-transform: uppercase; }
  .contact li { display: flex; align-items: center; gap: 8px; height: 19px; white-space: nowrap; }
  .contact svg { width: 13px; height: 11px; flex: none; }

  .footer-band { position: absolute; left: 0; bottom: 13px; width: 100%; height: 25px; background: var(--charcoal); }
  .footer-strip { position: absolute; left: 0; bottom: 0; width: 100%; height: 13px; background: var(--brand-blue); }
  .footer-chevrons { position: absolute; left: 425px; bottom: 13px; }
</style>
</head>
<body>
<main class="sheet">

  <section class="card card--front row-1" aria-label="Card front">
    <div class="brand"><span class="brand__dot"></span>Kestrel Developments</div>
  </section>

  <section class="card card--back row-1" aria-label="Card back">
    <div class="brand"><span class="brand__dot"></span>Kestrel Developments</div>
    <p class="person__name">Daniel Hartley</p>
    <svg class="person__rule" width="215" height="14" viewBox="0 0 215 14" aria-hidden="true">
      <polygon points="0,0 80,0 87,7 80,14 0,14" fill="var(--charcoal)"/>
      <polygon points="90,0 207,0 214,7 207,14 90,14 97,7" fill="var(--charcoal)"/>
    </svg>
    <p class="person__title">General Manager</p>
    <div class="divider"></div>
    <ul class="contact">
      <li><svg viewBox="0 0 13 11"><rect x="1" y="1" width="11" height="7" fill="none" stroke="currentColor" stroke-width="1.6"/><rect x="0" y="9" width="13" height="2" fill="currentColor"/></svg>+ (07) 3555 0192</li>
      <li><svg viewBox="0 0 13 11"><rect x="3" y="0" width="7" height="4" fill="currentColor"/><rect x="0" y="4" width="13" height="5" rx="1" fill="currentColor"/><rect x="3" y="8" width="7" height="3" fill="currentColor"/></svg>+ (07) 3555 0187</li>
      <li><svg viewBox="0 0 13 11"><rect x="0" y="1" width="13" height="9" fill="currentColor"/><polyline points="0,1 6.5,6 13,1" fill="none" stroke="#fff" stroke-width="1.2"/></svg>projects.kestreldev@mailbox.com</li>
      <li><svg viewBox="0 0 13 11"><polygon points="2,1 13,1 11,10 0,10" fill="currentColor"/></svg>PO Box 2745 Rivergate North QLD 4150</li>
    </ul>
    <div class="footer-band"></div>
    <div class="footer-strip"></div>
    <svg class="footer-chevrons" width="40" height="25" viewBox="0 0 40 25" aria-hidden="true">
      <polygon points="0,0 9,0 20,12.5 9,25 0,25 11,12.5" fill="var(--white)"/>
      <polygon points="17,0 26,0 37,12.5 26,25 17,25 28,12.5" fill="var(--white)"/>
    </svg>
  </section>

  <section class="card card--front row-2" aria-label="Card front">
    <div class="brand"><span class="brand__dot"></span>Kestrel Developments</div>
  </section>

  <section class="card card--back row-2" aria-label="Card back">
    <div class="brand"><span class="brand__dot"></span>Kestrel Developments</div>
    <p class="person__name">Daniel Hartley</p>
    <svg class="person__rule" width="215" height="14" viewBox="0 0 215 14" aria-hidden="true">
      <polygon points="0,0 80,0 87,7 80,14 0,14" fill="var(--charcoal)"/>
      <polygon points="90,0 207,0 214,7 207,14 90,14 97,7" fill="var(--charcoal)"/>
    </svg>
    <p class="person__title">General Manager</p>
    <div class="divider"></div>
    <ul class="contact">
      <li><svg viewBox="0 0 13 11"><rect x="1" y="1" width="11" height="7" fill="none" stroke="currentColor" stroke-width="1.6"/><rect x="0" y="9" width="13" height="2" fill="currentColor"/></svg>+ (07) 3555 0192</li>
      <li><svg viewBox="0 0 13 11"><rect x="3" y="0" width="7" height="4" fill="currentColor"/><rect x="0" y="4" width="13" height="5" rx="1" fill="currentColor"/><rect x="3" y="8" width="7" height="3" fill="currentColor"/></svg>+ (07) 3555 0187</li>
      <li><svg viewBox="0 0 13 11"><rect x="0" y="1" width="13" height="9" fill="currentColor"/><polyline points="0,1 6.5,6 13,1" fill="none" stroke="#fff" stroke-width="1.2"/></svg>projects.kestreldev@mailbox.com</li>
      <li><svg viewBox="0 0 13 11"><polygon points="2,1 13,1 11,10 0,10" fill="currentColor"/></svg>PO Box 2745 Rivergate North QLD 4150</li>
    </ul>
    <div class="footer-band"></div>
    <div class="footer-strip"></div>
    <svg class="footer-chevrons" width="40" height="25" viewBox="0 0 40 25" aria-hidden="true">
      <polygon points="0,0 9,0 20,12.5 9,25 0,25 11,12.5" fill="var(--white)"/>
      <polygon points="17,0 26,0 37,12.5 26,25 17,25 28,12.5" fill="var(--white)"/>
    </svg>
  </section>

</main>
</body>
</html>
```